Medical Clinic Group Looking for Website Design

We own and operate medical clinics and are looking looking to revamp our website. Our current website is www.brightpathcareclinics.ca We need our website to be more functional, user friendly, and easier to maintain.

```html
<!DOCTYPE html>
<html lang="en">
<head>
<meta charset="utf-8">
<title>BrightPath Care Clinics</title>
<link rel="stylesheet" href="https://fonts.googleapis.com/css2?family=Poppins:wght@400;500;600;700;800&display=swap">
<style>
:root{
  --teal:#33d1dc;
  --teal-dark:#1fb8c4;
  --ink:#1d1d1f;
  --body:#4a4a4a;
  --grey-band:#f3f3f3;
  --footer:#2b2b2b;
  --orange:#f58a1f;
  --white:#ffffff;
}
*{box-sizing:border-box;margin:0;padding:0}
html,body{width:1200px;height:3997px;overflow:hidden}
body{position:relative;background:var(--white);font-family:'Poppins',sans-serif;color:var(--body)}
.abs{position:absolute}
.brand{display:flex;align-items:center;gap:12px;color:var(--teal);font-weight:500;font-size:24px;letter-spacing:.2px;white-space:nowrap}
.brand-dot{width:44px;height:44px;border-radius:50%;background:var(--teal);opacity:.9;flex:none}
.site-header .brand{left:75px;top:51px}
.nav{left:466px;top:64px;font-weight:600;font-size:14px;color:var(--ink);letter-spacing:.3px}
.nav a{position:absolute;white-space:nowrap;text-decoration:none;color:inherit}
.btn{display:inline-flex;align-items:center;justify-content:center;background:var(--teal);color:var(--white);font-weight:600;border-radius:30px;text-decoration:none;white-space:nowrap}
.btn-outline{background:var(--white);color:var(--ink);border:2px solid var(--teal);font-weight:500}
.hero-art{left:0;top:137px}
.hero-copy{left:75px;top:262px;width:620px;color:var(--white)}
.hero-kicker{font-weight:600;font-size:19px;letter-spacing:.2px}
.hero-title{font-weight:700;font-size:51px;line-height:59px;margin-top:12px}
.hero-text{font-size:18px;line-height:31px;margin-top:10px;width:610px}
.hero-btn{position:absolute;left:0;top:335px;width:242px;height:55px;font-size:16px}
.dots{position:absolute;left:0;top:430px;display:flex;gap:8px}
.dots span{width:12px;height:12px;border-radius:50%;background:var(--teal)}
.dots span:first-child{background:var(--white)}
.band{background:var(--grey-band)}
.feature-title{font-weight:700;font-size:49px;color:var(--ink);line-height:1}
.feature-text{font-size:16px;line-height:28.5px;margin-top:28px;width:515px}
.feature-btn{position:absolute;width:146px;height:42px;font-size:17px}
.locations{left:0;top:2673px;width:1200px;height:560px;background:var(--teal)}
.section-title{font-weight:700;font-size:42px;text-align:center;width:100%;letter-spacing:.5px}
.locations .section-title{position:absolute;top:65px;color:var(--white)}
.card{position:absolute;top:153px;width:242px;height:332px;background:var(--white);text-align:center}
.card-img{width:242px;height:185px}
.card h3{font-weight:700;font-size:21px;color:var(--ink);margin-top:20px;white-space:nowrap}
.card p{font-size:16px;color:var(--body);margin-top:6px;white-space:nowrap}
.card .btn{width:152px;height:40px;font-size:14px;margin-top:16px}
.arrow{position:absolute;top:306px}
.contact{left:0;top:3290px;width:1200px;text-align:center}
.contact .section-title{color:#333}
.contact-lead{font-size:21px;line-height:34px;margin-top:14px}
.contact-line{font-weight:600;font-size:20px;color:var(--orange);margin-top:12px}
.contact .btn{width:144px;height:42px;font-size:16px;margin-top:22px}
.contact-note{font-size:13px;line-height:24px;margin-top:26px;color:#444}
.site-footer{left:0;top:3686px;width:1200px;height:311px;background:var(--footer);color:var(--white)}
.site-footer .brand{position:absolute;left:75px;top:70px;font-size:22px}
.site-footer .brand-dot{width:40px;height:40px}
.copy{position:absolute;left:75px;top:164px;font-size:13px;line-height:25px}
.socials{position:absolute;left:75px;top:230px;display:flex;gap:22px}
.socials span{width:22px;height:22px;border-radius:4px;background:var(--white)}
.foot-head{position:absolute;top:64px;font-weight:600;font-size:20px;color:var(--teal)}
.foot-links{position:absolute;left:487px;top:101px;list-style:none;font-size:15px;line-height:35px}
.foot-contact{position:absolute;left:793px;top:101px;font-size:15px;line-height:28px;list-style:none}
.foot-contact li{position:relative;padding-left:34px;margin-bottom:10px}
.foot-contact svg{position:absolute;left:0;top:6px}
</style>
</head>
<body>

<header class="site-header">
  <div class="brand abs"><span class="brand-dot"></span>BrightPath Care Clinics</div>
  <nav class="nav abs">
    <a style="left:0">LOCATIONS</a>
    <a style="left:125px">FOR PATIENTS</a>
    <a style="left:268px">FOR PROVIDERS</a>
    <a style="left:423px">ABOUT US</a>
  </nav>
  <a class="btn abs" style="left:979px;top:51px;width:146px;height:44px;font-size:14px">BOOK ONLINE</a>
</header>

<section class="hero">
  <svg class="hero-art abs" width="1200" height="910" viewBox="0 0 1200 910">
    <defs>
      <linearGradient id="heroGrad" x1="0" y1="0" x2="1" y2="1">
        <stop offset="0" stop-color="#8a8375"/>
        <stop offset=".45" stop-color="#3eaab0"/>
        <stop offset=".8" stop-color="#c9c1b6"/>
        <stop offset="1" stop-color="#6f8a84"/>
      </linearGradient>
    </defs>
    <path d="M0 605 L1010 900 Q1095 915 1140 820 L1200 640 L1200 680 L1140 860 Q1090 925 1000 905 Z" fill="var(--teal)"/>
    <path role="img" aria-label="Nurse helping an older patient use a smartphone" d="M0 0 H1200 V510 L1130 800 Q1095 900 1010 880 L0 605 Z" fill="url(#heroGrad)"/>
  </svg>
  <div class="hero-copy abs">
    <div class="hero-kicker">EASY ACCESS TO CARE WHEN YOU NEED IT</div>
    <h1 class="hero-title">Online Appointment<br>Booking Now Available<br>to all Patients</h1>
    <p class="hero-text">BrightPath Care Clinics continues to create options that better suit your lifestyle. Book your appointment when it's convenient for you, even if you don't have a family doctor.</p>
    <a class="btn hero-btn">Book An Appointment</a>
    <div class="dots"><span></span><span></span><span></span><span></span></div>
  </div>
</section>

<section class="feature">
  <div class="band abs" style="left:442px;top:1116px;width:758px;height:366px"></div>
  <svg class="abs" style="left:75px;top:1038px" width="530" height="530" viewBox="0 0 530 530" role="img" aria-label="Doctor reviewing a tablet with a patient in a hospital bed">
    <path d="M265 0 L530 265 L265 530 L0 265 Z" fill="var(--teal)" transform="translate(-4 10)"/>
    <rect x="90" y="90" width="350" height="350" rx="24" transform="rotate(45 265 265)" fill="#9ab8c8"/>
  </svg>
  <div class="abs" style="left:615px;top:1175px">
    <h2 class="feature-title">Our Services</h2>
    <p class="feature-text">Sed ut perspiciatis unde omnis iste natus error sit voluptatem accusantium doloremque laudantium, totam rem aperiam, eaque ipsa quae ab illo inventore veritatis et quasi archit ecto beatae vitae dicta sunt explicabo.</p>
  </div>
  <a class="btn feature-btn" style="left:616px;top:1384px">Read More</a>

  <div class="band abs" style="left:0;top:1633px;width:760px;height:366px"></div>
  <svg class="abs" style="left:600px;top:1550px" width="530" height="530" viewBox="0 0 530 530" role="img" aria-label="Couple smiling at a laptop together">
    <path d="M265 0 L530 265 L265 530 L0 265 Z" fill="var(--teal)" transform="translate(6 -6)"/>
    <rect x="90" y="90" width="350" height="350" rx="24" transform="rotate(45 265 265)" fill="#a9b3b8"/>
  </svg>
  <div class="abs" style="left:75px;top:1676px">
    <h2 class="feature-title">Find a Provider</h2>
    <p class="feature-text">Sed ut perspiciatis unde omnis iste natus error sit voluptatem accusantium doloremque laudantium, totam rem aperiam, eaque ipsa quae ab illo inventore veritatis et quasi archit ecto beatae vitae dicta sunt explicabo.</p>
  </div>
  <a class="btn feature-btn" style="left:75px;top:1886px">Read More</a>

  <div class="band abs" style="left:442px;top:2147px;width:758px;height:364px"></div>
  <svg class="abs" style="left:75px;top:2063px" width="530" height="530" viewBox="0 0 530 530" role="img" aria-label="Nurse with a tablet talking with a senior man">
    <path d="M265 0 L530 265 L265 530 L0 265 Z" fill="var(--teal)" transform="translate(-4 10)"/>
    <rect x="90" y="90" width="350" height="350" rx="24" transform="rotate(45 265 265)" fill="#6f86a6"/>
  </svg>
  <div class="abs" style="left:615px;top:2176px">
    <h2 class="feature-title">Patient Resources</h2>
    <p class="feature-text">Sed ut perspiciatis unde omnis iste natus error sit voluptatem accusantium doloremque laudantium, totam rem aperiam, eaque ipsa quae ab illo inventore veritatis et quasi archit ecto beatae vitae dicta sunt explicabo.</p>
  </div>
  <a class="btn feature-btn" style="left:616px;top:2385px">Read More</a>
</section>

<section class="locations abs">
  <h2 class="section-title">OUR LOCATIONS</h2>
  <svg class="arrow" style="left:42px" width="20" height="32" viewBox="0 0 20 32"><path d="M16 3 L4 16 L16 29" fill="none" stroke="#fff" stroke-width="3"/></svg>
  <svg class="arrow" style="left:1140px" width="20" height="32" viewBox="0 0 20 32"><path d="M4 3 L16 16 L4 29" fill="none" stroke="#fff" stroke-width="3"/></svg>
  <article class="card" style="left:75px">
    <div class="card-img" role="img" aria-label="Walk-in clinic storefront" style="background:linear-gradient(#3a78c4,#2f63a8)"></div>
    <h3>Kelowna Glenmore</h3><p>(Ridgeview Medical Clinic)</p>
    <a class="btn btn-outline">View Direction</a>
  </article>
  <article class="card" style="left:345px">
    <div class="card-img" role="img" aria-label="Clinic glass entrance" style="background:linear-gradient(#7f8a90,#3d4448)"></div>
    <h3>Kelowna - Pandosy</h3><p style="font-size:15px">(Sports Medicine &amp; Physiatry)</p>
    <a class="btn btn-outline">View Direction</a>
  </article>
  <article class="card" style="left:615px">
    <div class="card-img" role="img" aria-label="Clinic building with trees" style="background:linear-gradient(#9fb4b8,#5f7d5a)"></div>
    <h3 style="font-size:20px">Kelowna - Springfield</h3><p>(Unity Medical Group)</p>
    <a class="btn btn-outline">View Direction</a>
  </article>
  <article class="card" style="left:885px">
    <div class="card-img" role="img" aria-label="Medical clinic strip mall front" style="background:linear-gradient(#a8b8cf,#8e8a86)"></div>
    <h3>Lake Country</h3><p style="font-size:14px">(Lakeshore Bay Medical Clinic)</p>
    <a class="btn btn-outline">View Direction</a>
  </article>
</section>

<section class="contact abs">
  <h2 class="section-title">CONTACT US</h2>
  <p class="contact-lead">BrightPath Care Clinics is focused on our patients first. Connect with us to stay up to<br>date with current news and upcoming events.</p>
  <p class="contact-line">Phone: 250.555.0142&nbsp; Email: hello@brightpathcareclinics.ca</p>
  <a class="btn">Contact Us</a>
  <p class="contact-note">Please do not send medical questions to this email. If you have a medical question, contact your doctor's office directly.<br>Visit our locations page or click here to find contact information for each of our locations.</p>
</section>

<footer class="site-footer abs">
  <div class="brand"><span class="brand-dot"></span>BrightPath Care Clinics</div>
  <p class="copy">Copyright ©2022 by Company Name<br>All Right Reserved</p>
  <div class="socials"><span></span><span></span><span></span><span></span></div>
  <h4 class="foot-head" style="left:487px">SITE MAP</h4>
  <ul class="foot-links"><li>Locations</li><li>For Patients</li><li>For Providers</li><li>About Us</li><li>Book Online</li></ul>
  <h4 class="foot-head" style="left:793px">CONTACT US</h4>
  <ul class="foot-contact">
    <li><svg width="14" height="16" viewBox="0 0 14 16"><path d="M7 1a5 5 0 0 0-5 5c0 4 5 9 5 9s5-5 5-9a5 5 0 0 0-5-5z" fill="var(--teal)"/><circle cx="7" cy="6" r="2" fill="var(--footer)"/></svg>4820 Cedarline Rd,<br>Lake Country, BC V4V 2K8,<br>Canada</li>
    <li><svg width="14" height="14" viewBox="0 0 14 14"><path d="M3 1l3 3-2 2c1 2 2 3 4 4l2-2 3 3-2 2C6 13 1 8 1 3z" fill="var(--teal)"/></svg>250.555.0142</li>
    <li><svg width="15" height="12" viewBox="0 0 15 12"><rect x="0" y="1" width="15" height="10" rx="1" fill="var(--teal)"/><path d="M0 2l7.5 5L15 2" fill="none" stroke="var(--footer)" stroke-width="1.3"/></svg>hello@brightpathcareclinics.ca</li>
  </ul>
</footer>

</body>
</html>
```